Mira Bloom Fitness Coaching Project

I am a personal trainer based in London. My services include one-on-one PT sessions, bootcamps.
I would like the design to be minimalistic. With light colours: white, pink, purple.
I specialise in weight loss, flexibility, mobility.

Tessa Brogan
Personal Trainer
Email: tessa.brogan@quellmail.com
tel: 07700218493
Instagram: Mira Bloom

Target Market(s)

adults, mostly females (age 18-50).

Industry/Entity Type

Fitness

Contact Information for Business Card

Tessa Brogan
Personal Trainer
tel: 07700218493
Instagram: Mira Bloom

Font styles to use
Serif

Colors
eea4c8
fbd4d5
fdf9cf
cfeae6
cee9f5

Requirements
Nice to have
• minimalistic style
• easy to read and remember

```html
<!DOCTYPE html>
<html lang="en">
<head>
<meta charset="utf-8">
<title>Tessa Brogan – Personal Trainer Business Card</title>
<link href="https://fonts.googleapis.com/css2?family=Lora:wght@400;600;700&display=swap" rel="stylesheet">
<style>
  :root {
    --backdrop: #f3eff1;
    --blush: #fbd4d5;
    --rose: #eea4c8;
    --cream: #fdf9cf;
    --mint: #cfeae6;
    --sky: #cee9f5;
    --card-base: #fffdfd;
    --card-edge: #ecd9e2;
    --accent: #c4579a;
    --accent-deep: #9a5cb4;
    --ink: #5a4f58;
  }
  * { box-sizing: border-box; margin: 0; padding: 0; }
  html, body {
    width: 1200px;
    height: 969px;
    overflow: hidden;
    background: var(--backdrop);
    font-family: "Lora", Georgia, serif;
  }
  .canvas {
    position: relative;
    width: 1200px;
    height: 969px;
  }
  .business-card {
    position: absolute;
    left: 390px;
    top: 118px;
    width: 420px;
    height: 732px;
    border-radius: 26px;
    background: linear-gradient(180deg, var(--card-base) 0%, #fbf3f6 100%);
    border: 1px solid var(--card-edge);
    overflow: hidden;
    box-shadow: 0 10px 30px rgba(150, 100, 130, 0.14);
  }
  .portrait {
    position: absolute;
    left: 0;
    top: 0;
    width: 100%;
    height: 363px;
    background:
      radial-gradient(ellipse 45% 55% at 48% 42%, var(--cream) 0%, var(--blush) 55%, transparent 85%),
      linear-gradient(135deg, var(--rose) 0%, var(--blush) 55%, var(--sky) 100%);
    border-bottom: 3px solid var(--rose);
  }
  .details {
    position: absolute;
    left: 63px;
    right: 20px;
    top: 0;
    height: 100%;
  }
  .name {
    position: absolute;
    top: 440px;
    font-size: 34px;
    font-weight: 700;
    letter-spacing: 0.5px;
    line-height: 1.1;
    white-space: nowrap;
    background: linear-gradient(90deg, var(--accent) 0%, var(--accent-deep) 100%);
    -webkit-background-clip: text;
    background-clip: text;
    color: transparent;
    text-transform: uppercase;
  }
  .role {
    position: absolute;
    top: 486px;
    font-size: 15px;
    font-weight: 400;
    color: var(--ink);
    letter-spacing: 0.8px;
    text-transform: uppercase;
  }
  .contact-list {
    position: absolute;
    top: 526px;
    list-style: none;
  }
  .contact-item {
    display: flex;
    align-items: center;
    height: 24px;
    font-size: 15px;
    color: var(--ink);
    letter-spacing: 0.3px;
    white-space: nowrap;
    text-transform: uppercase;
  }
  .contact-icon {
    width: 14px;
    height: 14px;
    margin-right: 11px;
    flex: none;
    fill: var(--accent);
  }
  .social-mark {
    width: 12px;
    height: 12px;
    margin: 0 12px 0 1px;
    background: var(--accent);
    border-radius: 2px;
    flex: none;
  }
  .service-label {
    position: absolute;
    top: 613px;
    font-size: 15px;
    font-weight: 700;
    color: var(--accent);
    letter-spacing: 0.6px;
    text-transform: uppercase;
  }
  .service-text {
    position: absolute;
    top: 639px;
    font-size: 15px;
    color: var(--ink);
    letter-spacing: 0.3px;
    text-transform: uppercase;
  }
</style>
</head>
<body>
<main class="canvas">
  <article class="business-card">
    <div class="portrait" role="img" aria-label="Portrait photo of the personal trainer smiling, soft warm light"></div>
    <div class="details">
      <h1 class="name">Tessa Brogan</h1>
      <p class="role">Personal Trainer</p>
      <ul class="contact-list">
        <li class="contact-item">
          <svg class="contact-icon" viewBox="0 0 24 24" aria-hidden="true"><path d="M6.6 10.8a15.1 15.1 0 0 0 6.6 6.6l2.2-2.2a1 1 0 0 1 1-.25 11.4 11.4 0 0 0 3.6.57 1 1 0 0 1 1 1V20a1 1 0 0 1-1 1A17 17 0 0 1 3 4a1 1 0 0 1 1-1h3.5a1 1 0 0 1 1 1c0 1.25.2 2.45.57 3.6a1 1 0 0 1-.25 1z"/></svg>
          07700218493
        </li>
        <li class="contact-item">
          <svg class="contact-icon" viewBox="0 0 24 24" aria-hidden="true"><path d="M3 5h18a1 1 0 0 1 1 1v12a1 1 0 0 1-1 1H3a1 1 0 0 1-1-1V6a1 1 0 0 1 1-1zm9 7.2L20 7H4z"/></svg>
          tessa.brogan@quellmail.com
        </li>
        <li class="contact-item">
          <span class="social-mark" aria-hidden="true"></span>
          Mira Bloom
        </li>
      </ul>
      <h2 class="service-label">Service</h2>
      <p class="service-text">PT Sessions, Bootcamps.</p>
    </div>
  </article>
</main>
</body>
</html>
```